Telecommunications/Power civil contractor needs business card design

Were a new telecommunications/power underground civil contractor that is looking for a new business card design. Our company colours are silver or grey and orange. Feel free to use the white background logo or the black background logo.

Target Market(s)

Local contractors, utility companies, private sector mining/energy companies, developers.

Industry/Entity Type

Telecommunications

Contact Information for Business Card

Each card will need the following info:
Persons name:
Title:
E-mail:
Phone number:
Shop Address:
Mailing Address:

Requirements
Must have
• Each card will need the following info:
• Persons name:
• Title:
• E-mail:
• Phone number:
• Shop Address:
• Mailing Address:

```html
<!DOCTYPE html>
<html lang="en">
<head>
<meta charset="utf-8">
<title>Trenchline Contracting – Business Card</title>
<link rel="stylesheet" href="https://fonts.googleapis.com/css2?family=Open+Sans:wght@400;600;700&display=swap">
<style>
  :root {
    --orange: #f05a24;
    --orange-deep: #e8531f;
    --grey: #5d5f61;
    --grey-text: #555759;
    --white: #ffffff;
    --page: #e9e7e4;
  }
  * { margin: 0; padding: 0; box-sizing: border-box; }
  html, body { width: 1200px; height: 843px; overflow: hidden; }
  body {
    background: var(--page);
    font-family: "Open Sans", Arial, sans-serif;
    display: flex;
    flex-direction: column;
    align-items: center;
    justify-content: center;
    gap: 40px;
  }
  .card {
    width: 640px;
    height: 366px;
    position: relative;
    box-shadow: 0 4px 14px rgba(0,0,0,0.18);
  }
  /* Front */
  .card--front {
    background: linear-gradient(180deg, #f26a30 0%, var(--orange-deep) 100%);
    display: flex;
    align-items: center;
    justify-content: center;
    gap: 22px;
    color: var(--white);
  }
  .brand-dot {
    width: 64px; height: 64px;
    border: 5px solid currentColor;
    border-radius: 50%;
    flex: none;
  }
  .brand-name {
    font-weight: 700;
    line-height: 1.05;
    letter-spacing: 1px;
  }
  .brand-name .line-1 { display: block; font-size: 40px; }
  .brand-name .line-2 { display: block; font-size: 17px; letter-spacing: 2.4px; }

  /* Back */
  .card--back { background: var(--white); }
  .card--back .brand {
    position: absolute;
    right: 40px;
    top: 92px;
    display: flex;
    align-items: center;
    gap: 14px;
    color: var(--grey);
  }
  .card--back .brand-dot { width: 52px; height: 52px; border-width: 4px; color: var(--orange); }
  .card--back .brand-name .line-1 { font-size: 30px; }
  .card--back .brand-name .line-2 { font-size: 13px; letter-spacing: 1.8px; }

  .contact {
    position: absolute;
    left: 44px;
    top: 138px;
    color: var(--grey-text);
  }
  .contact__name {
    color: var(--orange);
    font-size: 22px;
    font-weight: 600;
    letter-spacing: 0.5px;
    line-height: 1.1;
  }
  .contact__title { font-size: 17px; margin-bottom: 14px; }
  .contact__list { list-style: none; font-size: 16px; line-height: 26px; }
  .contact__list li { display: flex; align-items: center; gap: 10px; }
  .contact__list svg { width: 14px; height: 14px; flex: none; }

  .address {
    position: absolute;
    left: 326px;
    top: 262px;
    padding-left: 18px;
    border-left: 2px solid var(--orange);
    font-size: 16px;
    line-height: 22px;
    color: var(--grey-text);
  }
</style>
</head>
<body>
  <section class="card card--front" aria-label="Business card front">
    <span class="brand-dot"></span>
    <p class="brand-name"><span class="line-1">TRENCHLINE</span><span class="line-2">CONTRACTING INC</span></p>
  </section>

  <section class="card card--back" aria-label="Business card back">
    <div class="brand">
      <span class="brand-dot"></span>
      <p class="brand-name"><span class="line-1">TRENCHLINE</span><span class="line-2">CONTRACTING INC</span></p>
    </div>

    <div class="contact">
      <h1 class="contact__name">EVAN MARSH</h1>
      <p class="contact__title">CEO/Founder</p>
      <ul class="contact__list">
        <li>
          <svg viewBox="0 0 14 14" aria-hidden="true"><path fill="#f05a24" d="M3 1l2 3-1.2 1.2c.8 1.7 2.2 3.1 3.9 3.9L9 8l3 2-1 2.6C6 12.8 1.2 8 1.4 3z"/></svg>
          555 014 2290
        </li>
        <li>
          <svg viewBox="0 0 14 14" aria-hidden="true"><rect x="1" y="3" width="12" height="8.5" fill="#f05a24"/><path d="M1 3l6 4.5L13 3" fill="none" stroke="#fff" stroke-width="1.2"/></svg>
          evan@trenchline.com
        </li>
        <li>
          <svg viewBox="0 0 14 14" aria-hidden="true"><circle cx="7" cy="7" r="6" fill="#f05a24"/><path d="M1 7h12M7 1c-2.5 3-2.5 9 0 12M7 1c2.5 3 2.5 9 0 12" fill="none" stroke="#fff" stroke-width="1"/></svg>
          www.trenchline.com
        </li>
      </ul>
    </div>

    <address class="address" style="font-style:normal">
      4120 Birchwood Road<br>
      Fairbanks, Alaska 99701
    </address>
  </section>
</body>
</html>
```